Webbanner-Design für Fachhandel für Medizinprodukte
Zielgruppe
wir sind ein Fachhandel für Medizinprodukte.
Aufgabenstellung
-Slider / Banner
-1920 x 340
-Es muss ein intersannter Satz auf dem Bild sein, der einläd zu klicken.
-https://www.korvantiq.de/
- folgender Artikel soll beworben werden:
-https://www.korvantiq.de/fingerpulsoximeter-tq418-pulsoximeter-weiss-2916
-Design soll gut zur Seite passen.
-Das Bild kann von der Seite verwendet werden.
-Gerne können zusätzlich auch Stockbilder verarbeitet werden.

```html
<!DOCTYPE html>
<html lang="de">
<head>
<meta charset="utf-8">
<title>KORVANTIQ – Fingerpulsoximeter TQ418 Banner</title>
<link href="https://fonts.googleapis.com/css2?family=Montserrat:wght@700;800&display=swap" rel="stylesheet">
<style>
  :root {
    --stage: #e0e0de;
    --banner-bg: #efefef;
    --green: #46ae4c;
    --green-dark: #37913d;
    --white: #ffffff;
    --product-tone: #f6f6f6;
    --product-shade: #d9d9d9;
  }
  * { margin: 0; padding: 0; box-sizing: border-box; }
  html, body {
    width: 1200px; height: 495px; overflow: hidden;
    background: var(--stage);
    font-family: "Montserrat", Arial, sans-serif;
  }
  .banner {
    position: absolute; left: 90px; top: 156px;
    width: 1020px; height: 180px;
    background: var(--banner-bg);
    overflow: hidden;
  }
  .banner__shapes { position: absolute; inset: 0; }
  .product-photo {
    position: absolute; left: 61px; top: 29px;
    width: 168px; height: 121px;
    border-radius: 12px;
    background: linear-gradient(160deg, var(--product-tone) 0%, var(--product-shade) 100%);
  }
  .model-tag {
    position: absolute; left: 240px; top: 52px;
    width: 100px; text-align: center;
    color: var(--white); font-weight: 700;
    font-size: 35px; line-height: 38px;
  }
  .headline {
    position: absolute; left: 397px; top: 24px;
    color: var(--white); font-weight: 800;
    font-size: 62px; line-height: 67px;
    letter-spacing: 1px;
    white-space: nowrap;
  }
  .brand {
    position: absolute; left: 825px; top: 28px;
    color: var(--green); font-weight: 800;
    font-size: 21px; letter-spacing: 0.3px;
  }
  .cta {
    position: absolute; left: 831px; top: 104px;
    width: 156px; height: 49px;
    background: var(--green); color: var(--white);
    border-radius: 8px;
    display: flex; align-items: center; justify-content: center;
    font-weight: 700; font-size: 16px; text-decoration: none;
  }
</style>
</head>
<body>
  <div class="banner">
    <svg class="banner__shapes" width="1020" height="180" viewBox="0 0 1020 180">
      <path d="M207 0 H798 V180 H181 Q176 80 207 0 Z" fill="var(--green)"/>
      <path d="M228 41 H347 Q372 90 347 140 H228 Z" fill="var(--green-dark)"/>
    </svg>
    <div class="product-photo" role="img" aria-label="Weißes Fingerpulsoximeter TQ418 mit leuchtendem Display"></div>
    <div class="model-tag">TQ<br>418</div>
    <div class="headline">SCHNELL<br>&amp; GENAUE</div>
    <div class="brand">KORVANTIQ</div>
    <a class="cta" href="https://www.korvantiq.de/fingerpulsoximeter-tq418-pulsoximeter-weiss-2916">Jetzt Kaufen</a>
  </div>
</body>
</html>
```